Varelko App for Smart Devices IoT WiFi Electronic

Varelko is a siren manufacturer. This application is used for the company's products that have a Wi-Fi connection and an internet connection, which can be configured and activated remotely through this application. In addition, this application is used to activate the siren at specific times for the start and end of shifts in companies and schools. Users will be siren installers and IT or HR managers.
In addition to activating motorized sirens timers, some siren models have speakers and allow you to play TTS (text to speech) audio, audio recorded by the user on the phone and upload audio (mp3) with playlist programming with start and end times.
Application screens: home with dashboard (one dashboard for each category). Device categories: timers, speakers, motorized siren. Screen for requesting evaluation in the Play Store. Screen for registering the user profile. Screen for registering devices according to their category (timers, speakers, motorized siren). Screen for registering device groups. Screen for pairing the device on the client's Wi-Fi network. Screen for registering activation times. Screen for uploading MP3 audios. Screen for registering playlists with audio selection, start and end times. Screen for recording audio for later sending to the speakers. Screen for converting text to speech and sending to the speakers. It is important to have a time picker with the day of the week to program the activation times and playlist.

Target Market(s)

Schools, Companies and Stores.

Industry/Entity Type

IoT

Font styles to use
Sans Serif
Other font styles liked:
• roboto

Colors
FFC000
F8CF3A
FAE287
FDF2CF
FEFAEE

Requirements
Must have
• time picker with weekdays for timer programming feature.
Nice to have
• app review request screen on play store

```html
<!DOCTYPE html>
<html lang="en">
<head>
<meta charset="utf-8">
<title>Varelko – Siren Timer App Screens</title>
<link rel="stylesheet" href="https://fonts.googleapis.com/css2?family=Inter:ital,wght@0,400;0,500;0,600;0,700;1,400&display=swap">
<style>
  :root{
    --stage:#474747;
    --screen:#060b28;
    --card:#0a1033;
    --card-line:#161d45;
    --chip:#141a3c;
    --icon-tile:#3a2f14;
    --yellow:#ffc000;
    --yellow-soft:#f8cf3a;
    --cream:#fdf2cf;
    --text:#ffffff;
    --muted:#c9ccd8;
  }
  *{box-sizing:border-box;margin:0;padding:0}
  html,body{width:1200px;height:714px;overflow:hidden;background:var(--stage)}
  body{font-family:"Inter",sans-serif;color:var(--text)}
  .board{position:absolute;left:0;top:0;width:2000px;height:1190px;transform:scale(.6);transform-origin:0 0}
  .screen{position:absolute;top:107px;width:375px;background:var(--screen);overflow:hidden}
  .screen > *{position:absolute}
  .time{left:24px;top:8px;font-size:15px;font-weight:600}
  .status-icons{right:24px;top:10px}
  .brand{left:24px;top:48px;font-size:30px;font-weight:500;color:var(--yellow);letter-spacing:-.5px}
  .nav{right:22px;top:50px;display:flex;gap:13px}
  .nav span{width:32px;height:32px;border-radius:50%;background:var(--chip);display:flex;align-items:center;justify-content:center}
  .title{left:0;width:100%;top:131px;text-align:center;font-size:20px;font-weight:600}
  .card{background:var(--card);border:1px solid var(--card-line);border-radius:3px}
  /* screen 1 */
  .shift{left:24px;top:174px;width:327px;height:78px}
  .shift .clock{position:absolute;left:9px;top:18px;width:40px;height:40px;border-radius:50%;background:var(--icon-tile);display:flex;align-items:center;justify-content:center}
  .shift h3{position:absolute;left:61px;top:17px;font-size:15px;font-weight:500}
  .shift p{position:absolute;left:61px;top:45px;font-size:13px;color:var(--muted)}
  .toggle{position:absolute;right:14px;top:16px;width:38px;height:22px;border-radius:11px;background:var(--yellow)}
  .toggle::after{content:"";position:absolute;right:3px;top:3px;width:16px;height:16px;border-radius:50%;background:#fff}
  .section-head{left:24px;display:flex;align-items:center;gap:9px;font-size:18px;font-weight:600}
  .add-round{right:24px;top:290px;width:32px;height:32px;border-radius:50%;background:var(--chip);display:flex;align-items:center;justify-content:center}
  .schedule{left:24px;width:327px;height:73px}
  .schedule .tile{position:absolute;left:10px;top:10px;width:44px;height:50px;background:var(--icon-tile);border-radius:2px;display:flex;align-items:center;justify-content:center}
  .schedule .days{position:absolute;left:68px;top:8px;font-size:12px;color:var(--yellow)}
  .schedule .hours{position:absolute;left:68px;top:28px;font-size:14px;font-weight:600}
  .schedule .label{position:absolute;left:68px;top:49px;font-size:12px;color:var(--muted)}
  .schedule .actions{position:absolute;right:12px;top:21px;display:flex;gap:6px}
  .schedule .actions span{width:28px;height:28px;border-radius:50%;background:var(--chip);display:flex;align-items:center;justify-content:center}
  .schedule .audio{position:absolute;left:10px;top:78px;font-size:14px;font-weight:500}
  .schedule .audio-text{position:absolute;left:10px;top:100px;font-size:12px;color:var(--muted)}
  .status-note{left:24px;top:918px;width:330px;font-size:13px;font-style:italic;line-height:21px}
  /* screen 2 */
  .field-label{left:24px;font-size:14px;font-weight:500}
  .input{left:24px;width:327px;height:41px;padding:0 16px;display:flex;align-items:center;justify-content:space-between;font-size:13px;color:var(--muted)}
  .week{left:24px;top:460px;width:330px;display:flex;align-items:center;font-size:13px}
  .week b{font-weight:500;font-size:14px;width:126px}
  .radio{display:flex;align-items:center;gap:8px;color:var(--muted);margin-right:32px}
  .radio i{width:16px;height:16px;border-radius:50%;border:1.5px solid var(--muted);display:inline-block;position:relative}
  .radio.on i{border-color:var(--yellow)}
  .radio.on i::after{content:"";position:absolute;left:3px;top:3px;width:7px;height:7px;border-radius:50%;background:var(--yellow)}
  .radio.on{margin-right:0}
  .primary{left:24px;top:719px;width:327px;height:52px;background:var(--yellow);border-radius:3px;color:#0b0b0b;font-weight:700;font-size:18px;display:flex;align-items:center;justify-content:center}
  /* screen 3 */
  .device{left:24px;width:327px;height:45px;padding:0 16px;display:flex;align-items:center;justify-content:space-between;font-size:15px;font-weight:500}
  .device i{width:17px;height:17px;border-radius:50%;border:1.5px solid #6a6f88}
  /* screen 4 */
  .pair-text{left:0;width:100%;top:132px;text-align:center;font-size:16px;font-weight:600;line-height:26px}
  .pair-name{left:0;width:100%;text-align:center;font-size:18px;color:var(--muted)}
  .pair-graphic{left:0;top:0}
</style>
</head>
<body>
<div class="board">

  <!-- Screen: timers dashboard -->
  <section class="screen" style="left:107px;height:990px">
    <span class="time">9:41</span>
    <svg class="status-icons" width="60" height="12" viewBox="0 0 60 12" fill="#fff"><rect x="0" y="7" width="3" height="4"/><rect x="4" y="5" width="3" height="6"/><rect x="8" y="3" width="3" height="8"/><rect x="12" y="1" width="3" height="10"/><path d="M21 4a10 10 0 0 1 14 0l-1.5 1.5a8 8 0 0 0-11 0zM24 7a6 6 0 0 1 8 0L28 11z"/><rect x="38" y="1" width="20" height="10" rx="2.5" fill="none" stroke="#fff"/><rect x="40" y="3" width="16" height="6" rx="1"/></svg>
    <div class="brand">varelko</div>
    <div class="nav">
      <span><svg width="16" height="12" viewBox="0 0 16 12" fill="#fff"><path d="M0 4a11 11 0 0 1 16 0l-1.5 1.5a9 9 0 0 0-13 0zM3 7a7 7 0 0 1 10 0l-1.5 1.5a5 5 0 0 0-7 0zM8 12l-2-2a3 3 0 0 1 4 0z"/></svg></span>
      <span><svg width="13" height="13" viewBox="0 0 13 13" fill="#fff"><rect width="3.5" height="3.5"/><rect x="4.75" width="3.5" height="3.5"/><rect x="9.5" width="3.5" height="3.5"/><rect y="4.75" width="3.5" height="3.5"/><rect x="4.75" y="4.75" width="3.5" height="3.5"/><rect x="9.5" y="4.75" width="3.5" height="3.5"/><rect y="9.5" width="3.5" height="3.5"/><rect x="4.75" y="9.5" width="3.5" height="3.5"/><rect x="9.5" y="9.5" width="3.5" height="3.5"/></svg></span>
      <span><svg width="12" height="14" viewBox="0 0 12 14" fill="#fff"><circle cx="6" cy="3.5" r="3.2"/><path d="M0 14c0-4 2.5-6 6-6s6 2 6 6z"/></svg></span>
    </div>
    <h1 class="title">Motorized Sirens Timers</h1>

    <div class="card shift">
      <span class="clock"><svg width="20" height="20" viewBox="0 0 20 20" fill="none" stroke="#ffc000" stroke-width="1.5"><circle cx="10" cy="10" r="8.5"/><path d="M10 5v5l3 3"/></svg></span>
      <h3>Shift Timing</h3>
      <p>Activate the device for shift timing</p>
      <span class="toggle"></span>
    </div>

    <h2 class="section-head" style="top:295px"><svg width="16" height="16" viewBox="0 0 16 16" fill="none" stroke="#fff" stroke-width="2"><circle cx="8" cy="8" r="6.5"/><path d="M8 4.5V8l2 2"/></svg>Schedules</h2>
    <span class="add-round"><svg width="18" height="18" viewBox="0 0 18 18" stroke="#ffc000" stroke-width="2"><path d="M9 1v16M1 9h16"/></svg></span>

    <div class="card schedule" style="top:347px;height:128px">
      <span class="tile"><svg width="16" height="24" viewBox="0 0 16 24" fill="#ffc000"><rect x="4" y="0" width="8" height="14" rx="4"/><path d="M1 10a7 7 0 0 0 14 0" fill="none" stroke="#ffc000" stroke-width="2"/><rect x="7" y="17" width="2" height="5"/></svg></span>
      <span class="days">Weekdays</span><span class="hours">9:00 AM to 1:00 PM</span><span class="label">1st half session</span>
      <div class="actions"><span><svg width="12" height="12" viewBox="0 0 12 12" fill="none" stroke="#fff" stroke-width="1.5"><circle cx="6" cy="6" r="5"/><path d="M6 3v3l1.5 1.5"/></svg></span><span><svg width="12" height="12" viewBox="0 0 12 12" fill="#fff"><path d="M0 12l1-3.5L8.5 1l2.5 2.5L3.5 11z"/></svg></span></div>
      <span class="audio">Audio: Text to Speech</span>
      <span class="audio-text">The shfit has be started, Have a nice day</span>
    </div>

    <div class="card schedule" style="top:493px">
      <span class="tile"><svg width="26" height="22" viewBox="0 0 26 22" fill="none" stroke="#ffc000" stroke-width="2"><circle cx="13" cy="12" r="8"/><circle cx="13" cy="12" r="4"/><path d="M2 2v18M24 2v18"/></svg></span>
      <span class="days">Weekdays</span><span class="hours">1:00 PM to 2:00 PM</span><span class="label">Lunch Time</span>
      <div class="actions"><span><svg width="12" height="12" viewBox="0 0 12 12" fill="none" stroke="#fff" stroke-width="1.5"><circle cx="6" cy="6" r="5"/><path d="M6 3v3l1.5 1.5"/></svg></span><span><svg width="12" height="12" viewBox="0 0 12 12" fill="#fff"><path d="M0 12l1-3.5L8.5 1l2.5 2.5L3.5 11z"/></svg></span></div>
    </div>

    <div class="card schedule" style="top:582px">
      <span class="tile"><svg width="24" height="22" viewBox="0 0 24 22" fill="#ffc000"><path d="M2 8h16v6a6 6 0 0 1-6 6H8a6 6 0 0 1-6-6z"/><path d="M18 10h2a2.5 2.5 0 0 1 0 5h-2" fill="none" stroke="#ffc000" stroke-width="2"/><path d="M7 1v4M11 1v4" stroke="#ffc000" stroke-width="1.5"/></svg></span>
      <span class="days">Weekdays</span><span class="hours">4:00 PM to 4:20 PM</span><span class="label">Coffee Break</span>
      <div class="actions"><span><svg width="12" height="12" viewBox="0 0 12 12" fill="none" stroke="#fff" stroke-width="1.5"><circle cx="6" cy="6" r="5"/><path d="M6 3v3l1.5 1.5"/></svg></span><span><svg width="12" height="12" viewBox="0 0 12 12" fill="#fff"><path d="M0 12l1-3.5L8.5 1l2.5 2.5L3.5 11z"/></svg></span></div>
    </div>

    <div class="card schedule" style="top:672px">
      <span class="tile"><svg width="22" height="24" viewBox="0 0 22 24" fill="#ffc000"><path d="M1 1h10v22H1z"/><path d="M13 12h8M18 9l3 3-3 3" fill="none" stroke="#ffc000" stroke-width="2"/></svg></span>
      <span class="days">Weekdays</span><span class="hours">6:00 PM</span><span class="label">Signing out Time</span>
      <div class="actions"><span><svg width="12" height="12" viewBox="0 0 12 12" fill="none" stroke="#fff" stroke-width="1.5"><circle cx="6" cy="6" r="5"/><path d="M6 3v3l1.5 1.5"/></svg></span><span><svg width="12" height="12" viewBox="0 0 12 12" fill="#fff"><path d="M0 12l1-3.5L8.5 1l2.5 2.5L3.5 11z"/></svg></span></div>
    </div>

    <div class="card schedule" style="top:761px">
      <span class="tile"><svg width="24" height="22" viewBox="0 0 24 22" fill="#ffc000"><rect x="1" y="1" width="10" height="7"/><circle cx="6" cy="12" r="2.5"/><circle cx="18" cy="6" r="2.5"/><path d="M2 21v-4a4 4 0 0 1 8 0v4zM14 21v-9a4 4 0 0 1 8 0v9z"/></svg></span>
      <span class="days">Weekdays</span><span class="hours">9:00 AM to 12 PM</span><span class="label">Special Session</span>
      <div class="actions"><span><svg width="12" height="12" viewBox="0 0 12 12" fill="none" stroke="#fff" stroke-width="1.5"><circle cx="6" cy="6" r="5"/><path d="M6 3v3l1.5 1.5"/></svg></span><span><svg width="12" height="12" viewBox="0 0 12 12" fill="#fff"><path d="M0 12l1-3.5L8.5 1l2.5 2.5L3.5 11z"/></svg></span></div>
    </div>

    <h2 class="section-head" style="top:877px"><svg width="18" height="18" viewBox="0 0 18 18" fill="none" stroke="#fff" stroke-width="1.6"><rect x="5" y="5" width="12" height="12"/><path d="M1 13V1h12"/></svg>Status</h2>
    <p class="status-note">Next Ring of siren is at 1:00 PM to 2:00 PM which is lunch time (Siren alarm in 20 mins)</p>
  </section>

  <!-- Screen: add schedule -->
  <section class="screen" style="left:582px;height:821px">
    <span class="time">9:41</span>
    <svg class="status-icons" width="60" height="12" viewBox="0 0 60 12" fill="#fff"><rect x="0" y="7" width="3" height="4"/><rect x="4" y="5" width="3" height="6"/><rect x="8" y="3" width="3" height="8"/><rect x="12" y="1" width="3" height="10"/><path d="M21 4a10 10 0 0 1 14 0l-1.5 1.5a8 8 0 0 0-11 0zM24 7a6 6 0 0 1 8 0L28 11z"/><rect x="38" y="1" width="20" height="10" rx="2.5" fill="none" stroke="#fff"/><rect x="40" y="3" width="16" height="6" rx="1"/></svg>
    <div class="brand">varelko</div>
    <div class="nav">
      <span><svg width="16" height="12" viewBox="0 0 16 12" fill="#fff"><path d="M0 4a11 11 0 0 1 16 0l-1.5 1.5a9 9 0 0 0-13 0zM3 7a7 7 0 0 1 10 0l-1.5 1.5a5 5 0 0 0-7 0zM8 12l-2-2a3 3 0 0 1 4 0z"/></svg></span>
      <span><svg width="13" height="13" viewBox="0 0 13 13" fill="#fff"><rect width="3.5" height="3.5"/><rect x="4.75" width="3.5" height="3.5"/><rect x="9.5" width="3.5" height="3.5"/><rect y="4.75" width="3.5" height="3.5"/><rect x="4.75" y="4.75" width="3.5" height="3.5"/><rect x="9.5" y="4.75" width="3.5" height="3.5"/><rect y="9.5" width="3.5" height="3.5"/><rect x="4.75" y="9.5" width="3.5" height="3.5"/><rect x="9.5" y="9.5" width="3.5" height="3.5"/></svg></span>
      <span><svg width="12" height="14" viewBox="0 0 12 14" fill="#fff"><circle cx="6" cy="3.5" r="3.2"/><path d="M0 14c0-4 2.5-6 6-6s6 2 6 6z"/></svg></span>
    </div>
    <h1 class="title">Add the new schedules for siren</h1>

    <label class="field-label" style="top:186px">Title of Siren alarm</label>
    <div class="card input" style="top:214px">Enter alarm</div>
    <label class="field-label" style="top:277px">start time of siren</label>
    <div class="card input" style="top:305px">Select Time<svg width="12" height="12" viewBox="0 0 12 12" fill="none" stroke="#fff" stroke-width="1.5"><circle cx="6" cy="6" r="5"/><path d="M6 3v3l1.5 1.5"/></svg></div>
    <label class="field-label" style="top:368px">End time of siren</label>
    <div class="card input" style="top:396px">Select Time<svg width="12" height="12" viewBox="0 0 12 12" fill="none" stroke="#fff" stroke-width="1.5"><circle cx="6" cy="6" r="5"/><path d="M6 3v3l1.5 1.5"/></svg></div>
    <div class="week"><b>Week:</b><span class="radio"><i></i>Weekdays</span><span class="radio on"><i></i>Weekend</span></div>
    <label class="field-label" style="top:505px">Audio Format</label>
    <div class="card input" style="top:533px">MP3 Audio<svg width="10" height="6" viewBox="0 0 10 6" fill="none" stroke="#fff" stroke-width="1.5"><path d="M1 1l4 4 4-4"/></svg></div>
    <label class="field-label" style="top:601px">Choose audio from files</label>
    <div class="card input" style="top:629px">Audio file name<svg width="14" height="14" viewBox="0 0 14 14" fill="#fff"><path d="M7 0l4 4H8.5v5h-3V4H3z"/><path d="M0 10h2v2h10v-2h2v4H0z"/></svg></div>
    <div class="primary">ADD</div>
  </section>

  <!-- Screen: device list -->
  <section class="screen" style="left:1057px;height:813px">
    <span class="time">9:41</span>
    <svg class="status-icons" width="60" height="12" viewBox="0 0 60 12" fill="#fff"><rect x="0" y="7" width="3" height="4"/><rect x="4" y="5" width="3" height="6"/><rect x="8" y="3" width="3" height="8"/><rect x="12" y="1" width="3" height="10"/><path d="M21 4a10 10 0 0 1 14 0l-1.5 1.5a8 8 0 0 0-11 0zM24 7a6 6 0 0 1 8 0L28 11z"/><rect x="38" y="1" width="20" height="10" rx="2.5" fill="none" stroke="#fff"/><rect x="40" y="3" width="16" height="6" rx="1"/></svg>
    <div class="brand">varelko</div>
    <div class="nav">
      <span><svg width="16" height="12" viewBox="0 0 16 12" fill="#fff"><path d="M0 4a11 11 0 0 1 16 0l-1.5 1.5a9 9 0 0 0-13 0zM3 7a7 7 0 0 1 10 0l-1.5 1.5a5 5 0 0 0-7 0zM8 12l-2-2a3 3 0 0 1 4 0z"/></svg></span>
      <span><svg width="13" height="13" viewBox="0 0 13 13" fill="#fff"><rect width="3.5" height="3.5"/><rect x="4.75" width="3.5" height="3.5"/><rect x="9.5" width="3.5" height="3.5"/><rect y="4.75" width="3.5" height="3.5"/><rect x="4.75" y="4.75" width="3.5" height="3.5"/><rect x="9.5" y="4.75" width="3.5" height="3.5"/><rect y="9.5" width="3.5" height="3.5"/><rect x="4.75" y="9.5" width="3.5" height="3.5"/><rect x="9.5" y="9.5" width="3.5" height="3.5"/></svg></span>
      <span><svg width="12" height="14" viewBox="0 0 12 14" fill="#fff"><circle cx="6" cy="3.5" r="3.2"/><path d="M0 14c0-4 2.5-6 6-6s6 2 6 6z"/></svg></span>
    </div>
    <h1 class="title">Devices Available to connect</h1>
    <div class="card device" style="top:195px">Xyz timer<svg width="18" height="18" viewBox="0 0 18 18"><circle cx="9" cy="9" r="9" fill="#ffc000"/><path d="M5 9l3 3 5-6" fill="none" stroke="#060b28" stroke-width="2"/></svg></div>
    <div class="card device" style="top:262px">IT Siren abc<i></i></div>
    <div class="card device" style="top:328px">Support team speaker<i></i></div>
  </section>

  <!-- Screen: wi-fi pairing -->
  <section class="screen" style="left:1532px;height:813px">
    <span class="time">9:41</span>
    <svg class="status-icons" width="60" height="12" viewBox="0 0 60 12" fill="#fff"><rect x="0" y="7" width="3" height="4"/><rect x="4" y="5" width="3" height="6"/><rect x="8" y="3" width="3" height="8"/><rect x="12" y="1" width="3" height="10"/><path d="M21 4a10 10 0 0 1 14 0l-1.5 1.5a8 8 0 0 0-11 0zM24 7a6 6 0 0 1 8 0L28 11z"/><rect x="38" y="1" width="20" height="10" rx="2.5" fill="none" stroke="#fff"/><rect x="40" y="3" width="16" height="6" rx="1"/></svg>
    <div class="brand">varelko</div>
    <div class="nav">
      <span><svg width="16" height="12" viewBox="0 0 16 12" fill="#fff"><path d="M0 4a11 11 0 0 1 16 0l-1.5 1.5a9 9 0 0 0-13 0zM3 7a7 7 0 0 1 10 0l-1.5 1.5a5 5 0 0 0-7 0zM8 12l-2-2a3 3 0 0 1 4 0z"/></svg></span>
      <span><svg width="13" height="13" viewBox="0 0 13 13" fill="#fff"><rect width="3.5" height="3.5"/><rect x="4.75" width="3.5" height="3.5"/><rect x="9.5" width="3.5" height="3.5"/><rect y="4.75" width="3.5" height="3.5"/><rect x="4.75" y="4.75" width="3.5" height="3.5"/><rect x="9.5" y="4.75" width="3.5" height="3.5"/><rect y="9.5" width="3.5" height="3.5"/><rect x="4.75" y="9.5" width="3.5" height="3.5"/><rect x="9.5" y="9.5" width="3.5" height="3.5"/></svg></span>
      <span><svg width="12" height="14" viewBox="0 0 12 14" fill="#fff"><circle cx="6" cy="3.5" r="3.2"/><path d="M0 14c0-4 2.5-6 6-6s6 2 6 6z"/></svg></span>
    </div>
    <p class="pair-text">you will be connecting to Xyz timer to<br>your account using wi-fi pairing</p>
    <svg class="pair-graphic" width="375" height="813" viewBox="0 0 375 813">
      <circle cx="188" cy="428" r="138" fill="none" stroke="#0d1334" stroke-width="9"/>
      <path d="M188 290A138 138 0 0 1 212 564" fill="none" stroke="#ffc000" stroke-width="7"/>
      <circle cx="188" cy="428" r="104" fill="none" stroke="#fdf2cf" stroke-width="2.5"/>
      <circle cx="188" cy="428" r="62" fill="#ffc000"/>
      <g fill="none" stroke="#060b28" stroke-width="8" stroke-linecap="round">
        <path d="M152 418a52 52 0 0 1 72 0"/>
        <path d="M166 432a32 32 0 0 1 44 0"/>
      </g>
      <path d="M176 446a17 17 0 0 1 24 0L188 458z" fill="#060b28"/>
      <circle cx="188" cy="289" r="19" fill="#0d1334"/>
      <circle cx="188" cy="283" r="4.5" fill="#fff"/>
      <path d="M180 297c0-5 3.5-7 8-7s8 2 8 7z" fill="#fff"/>
      <circle cx="188" cy="566" r="19" fill="#0d1334"/>
      <circle cx="188" cy="567" r="6.5" fill="none" stroke="#fff" stroke-width="1.6"/>
      <path d="M188 564v3l2 1.5M181 560l3-3M195 560l-3-3" stroke="#fff" stroke-width="1.6" fill="none"/>
    </svg>
    <span class="pair-name" style="top:237px">abc</span>
    <span class="pair-name" style="top:595px">Xyz timer</span>
  </section>

</div>
</body>
</html>
```